Business Cards for a law firm

Business cards for our law firm. Use our silhoette logo and OAK PARTNERS - check our website (www.oakpartners.example)

Contact Information for Business Card

our silhouette logo, OAK PARTNERS, 800-555-0147, Dorian Pemberton, dorian@oakpartners.example

Requirements
Must have
• our silhouette logo, OAK PARTNERS, 800-555-0147, Dorian Pemberton, dorian@oakpartners.example

```html
<!DOCTYPE html>
<html lang="en">
<head>
<meta charset="utf-8">
<title>Oak Partners Business Cards</title>
<link href="https://fonts.googleapis.com/css2?family=Cinzel:wght@700&family=Arimo:wght@400;700&display=swap" rel="stylesheet">
<style>
  :root {
    --page-bg: #e4e4e4;
    --card-black: #000000;
    --deep-navy: #0a4068;
    --night: #03121d;
    --gold-light: #f7dc3c;
    --gold-mid: #d9a520;
    --gold-dark: #7a4a10;
    --icon-gold: #f2cc30;
    --text-white: #ffffff;
    --logo-fill: #e9edf1;
  }
  * { margin: 0; padding: 0; box-sizing: border-box; }
  html, body { width: 1200px; height: 1200px; overflow: hidden; background: var(--page-bg); }
  .canvas { position: relative; width: 1200px; height: 1200px; }

  .card { position: absolute; left: 200px; width: 799px; height: 457px; background: var(--card-black); overflow: hidden; }
  .card-front { top: 123px; }
  .card-back { top: 620px; }

  .brand-panel {
    position: absolute; left: 0; top: 0; width: 344px; height: 100%;
    background: radial-gradient(ellipse 420px 420px at 100% 0%, var(--deep-navy) 0%, var(--night) 60%, #000 100%);
  }
  .gold-divider {
    position: absolute; left: 344px; top: 0; width: 15px; height: 100%;
    background: linear-gradient(90deg, var(--gold-dark) 0%, var(--gold-light) 25%, var(--gold-mid) 55%, var(--gold-dark) 75%, var(--gold-light) 100%);
  }
  .logo-placeholder {
    position: absolute;
    background: linear-gradient(180deg, var(--logo-fill) 0%, #c9d2da 100%);
    opacity: 0.9;
  }
  .brand-name {
    position: absolute; font-family: "Cinzel", serif; font-weight: 700;
    color: var(--text-white); white-space: nowrap; letter-spacing: 0.5px;
    line-height: 1; transform: translateY(-50%);
  }
  .brand-panel .logo-placeholder { left: 37px; top: 199px; width: 39px; height: 59px; }
  .brand-panel .brand-name { left: 85px; top: 223px; font-size: 26px; }

  .contact-name {
    position: absolute; right: 37px; top: 220px; transform: translateY(-50%);
    font-family: "Arimo", sans-serif; font-weight: 700; font-size: 35px; line-height: 1;
    color: var(--text-white); white-space: nowrap;
  }
  .contact-list { position: absolute; right: 37px; top: 0; list-style: none; }
  .contact-item {
    position: absolute; right: 0; display: flex; align-items: center; gap: 10px;
    font-family: "Arimo", sans-serif; font-size: 21px; line-height: 1; color: var(--text-white); white-space: nowrap;
    transform: translateY(-50%);
  }
  .contact-item svg { width: 29px; height: 29px; flex: none; }
  .item-phone { top: 268px; }
  .item-email { top: 310px; }
  .item-web { top: 354px; }
  .item-address { top: 391px; }

  .back-top {
    position: absolute; left: 0; top: 0; width: 100%; height: 104px;
    background: linear-gradient(180deg, #000 0%, #020b12 60%, #06192a 100%);
  }
  .gold-band {
    position: absolute; left: 0; width: 100%; height: 17px;
    background: linear-gradient(180deg, var(--gold-light) 0%, var(--gold-mid) 35%, var(--gold-dark) 60%, var(--gold-light) 100%);
  }
  .band-top { top: 104px; }
  .band-bottom { top: 336px; }
  .back-bottom {
    position: absolute; left: 0; top: 353px; width: 100%; height: 104px;
    background: linear-gradient(180deg, #0c2232 0%, #03101a 50%, #000 100%);
  }
  .card-back .logo-placeholder { left: 66px; top: 155px; width: 97px; height: 146px; }
  .card-back .brand-name { left: 185px; top: 215px; font-size: 64px; }
</style>
</head>
<body>
<main class="canvas">
  <section class="card card-front" aria-label="Business card front">
    <div class="brand-panel">
      <div class="logo-placeholder" role="img" aria-label="Silhouette logo of two standing figures"></div>
      <p class="brand-name">OAK PARTNERS</p>
    </div>
    <div class="gold-divider"></div>
    <h1 class="contact-name">Dorian Pemberton</h1>
    <ul class="contact-list">
      <li class="contact-item item-phone">800-555-0147
        <svg viewBox="0 0 30 30" aria-hidden="true"><circle cx="15" cy="15" r="13.5" fill="none" stroke="var(--icon-gold)" stroke-width="1.6"/><path d="M10 8.5l2.5-.5 1.6 3.3-1.6 1.2c.8 1.8 2 3 3.8 3.8l1.2-1.6 3.3 1.6-.5 2.5c-5.5.3-10.6-4.8-10.3-10.3z" fill="var(--icon-gold)"/></svg>
      </li>
      <li class="contact-item item-email">dorian@oakpartners.example
        <svg viewBox="0 0 30 30" aria-hidden="true"><circle cx="15" cy="15" r="13.5" fill="none" stroke="var(--icon-gold)" stroke-width="1.6"/><rect x="8.5" y="10.5" width="13" height="9" fill="none" stroke="var(--icon-gold)" stroke-width="1.4"/><path d="M8.5 10.5l6.5 5 6.5-5" fill="none" stroke="var(--icon-gold)" stroke-width="1.4"/></svg>
      </li>
      <li class="contact-item item-web">www.oakpartners.example
        <svg viewBox="0 0 30 30" aria-hidden="true"><circle cx="15" cy="15" r="13.5" fill="none" stroke="var(--icon-gold)" stroke-width="1.6"/><circle cx="15" cy="15" r="8" fill="none" stroke="var(--icon-gold)" stroke-width="1.2"/><ellipse cx="15" cy="15" rx="3.5" ry="8" fill="none" stroke="var(--icon-gold)" stroke-width="1.2"/><path d="M7 15h16M8.2 11h13.6M8.2 19h13.6" stroke="var(--icon-gold)" stroke-width="1.1"/></svg>
      </li>
      <li class="contact-item item-address">Your Street, City, State, Country
        <svg viewBox="0 0 30 30" aria-hidden="true"><circle cx="15" cy="15" r="13.5" fill="none" stroke="var(--icon-gold)" stroke-width="1.6"/><path d="M15 23c-3.5-4.5-5.5-7.5-5.5-10a5.5 5.5 0 0 1 11 0c0 2.5-2 5.5-5.5 10z" fill="var(--icon-gold)"/><circle cx="15" cy="13" r="2" fill="#000"/></svg>
      </li>
    </ul>
  </section>

  <section class="card card-back" aria-label="Business card back">
    <div class="back-top"></div>
    <div class="gold-band band-top"></div>
    <div class="logo-placeholder" role="img" aria-label="Silhouette logo of two standing figures"></div>
    <p class="brand-name">OAK PARTNERS</p>
    <div class="gold-band band-bottom"></div>
    <div class="back-bottom"></div>
  </section>
</main>
</body>
</html>
```